VOMRA Pty Ltd Business Card

Looking for a simple yet eye-catching double-sided business card design using my company logo on one side and contact details on the other.

Target Market(s)

Government

Industry/Entity Type

Communication Systems Engineering

Contact Information for Business Card

VOMRA Pty Ltd

Requirements
Nice to have
• Would be great to have a QR code so details can be scanned into contacts

```html
<!DOCTYPE html>
<html lang="en">
<head>
<meta charset="utf-8">
<title>VOMRA Pty Ltd Business Card</title>
<link href="https://fonts.googleapis.com/css2?family=Montserrat:wght@400;500;700&display=swap" rel="stylesheet">
<style>
  :root {
    --backdrop: #d9d9d6;
    --card: #ffffff;
    --slate: #37434b;
    --ink: #111417;
    --text: #2f3a41;
  }
  * { box-sizing: border-box; margin: 0; padding: 0; }
  html, body { width: 1200px; height: 801px; overflow: hidden; }
  body {
    background: var(--backdrop);
    font-family: "Montserrat", Arial, sans-serif;
    color: var(--text);
    display: flex;
    align-items: center;
    justify-content: center;
    gap: 40px;
  }
  .card {
    position: relative;
    width: 540px;
    height: 310px;
    background: var(--card);
    border-radius: 18px;
    overflow: hidden;
    box-shadow: 0 10px 24px rgba(0,0,0,0.18);
  }
  .wave { position: absolute; inset: 0; width: 100%; height: 100%; }
  .brand {
    position: absolute;
    display: flex;
    align-items: center;
    gap: 12px;
    color: var(--slate);
    font-weight: 700;
  }
  .brand-dot {
    border: 3px solid var(--slate);
    border-radius: 50%;
  }
  .front .brand { left: 34px; top: 96px; font-size: 40px; letter-spacing: 1px; }
  .front .brand-dot { width: 34px; height: 34px; }
  .divider {
    position: absolute;
    left: 268px;
    top: 34px;
    width: 1.5px;
    height: 168px;
    background: var(--slate);
  }
  .contact {
    position: absolute;
    left: 288px;
    top: 34px;
    font-size: 12px;
    line-height: 1.45;
  }
  .contact-name { font-size: 19px; font-weight: 700; color: var(--slate); letter-spacing: 0.5px; line-height: 1.1; }
  .contact-role { font-size: 12.5px; margin-bottom: 12px; }
  .contact-line { display: flex; align-items: center; gap: 7px; }
  .contact-line svg { width: 11px; height: 11px; fill: var(--slate); flex: none; }
  .contact-address { margin-top: 12px; }
  .back .brand { left: 50%; top: 50%; transform: translate(-50%, -50%); font-size: 68px; letter-spacing: 2px; gap: 20px; }
  .back .brand-dot { width: 56px; height: 56px; border-width: 4px; }
</style>
</head>
<body>
  <section class="card front" aria-label="Business card, contact side">
    <svg class="wave" viewBox="0 0 540 310" preserveAspectRatio="none" aria-hidden="true">
      <path d="M0,296 C180,296 250,270 330,230 C410,190 450,180 540,178 L540,310 L0,310 Z" fill="var(--slate)"/>
      <path d="M0,290 C180,290 250,262 330,222 C410,182 450,172 540,170" fill="none" stroke="var(--ink)" stroke-width="4"/>
    </svg>
    <div class="brand"><span class="brand-dot"></span><span class="brand-name">VOMRA</span></div>
    <div class="divider"></div>
    <div class="contact">
      <p class="contact-name">DANIEL HART</p>
      <p class="contact-role">Managing Director</p>
      <p class="contact-line">
        <svg viewBox="0 0 24 24"><path d="M6.6 10.8a15.1 15.1 0 0 0 6.6 6.6l2.2-2.2a1 1 0 0 1 1-.25 11.4 11.4 0 0 0 3.6.57 1 1 0 0 1 1 1V20a1 1 0 0 1-1 1A17 17 0 0 1 3 4a1 1 0 0 1 1-1h3.5a1 1 0 0 1 1 1c0 1.25.2 2.45.57 3.57a1 1 0 0 1-.25 1z"/></svg>
        02 5550 1842</p>
      <p class="contact-line">
        <svg viewBox="0 0 24 24"><path d="M2 5h20v14H2z M2 5l10 8 10-8" stroke="#fff" stroke-width="1.5"/></svg>
        admin@vomra.com.au</p>
      <p class="contact-line">
        <svg viewBox="0 0 24 24"><circle cx="12" cy="12" r="10"/><path d="M2 12h20M12 2c3 3 3 17 0 20M12 2c-3 3-3 17 0 20" stroke="#fff" stroke-width="1.5" fill="none"/></svg>
        www.vomra.com.au</p>
      <p class="contact-address">14-16 Harlow Lane Redfern<br>NSW 2016 Australia</p>
    </div>
  </section>

  <section class="card back" aria-label="Business card, logo side">
    <div class="brand"><span class="brand-dot"></span><span class="brand-name">VOMRA</span></div>
  </section>
</body>
</html>
```